International Trade Consulting Firm Seeks Quality Newsletter Design

Our company provides consulting services to Pinnacle 300 type companies. We compete with the largest consulting companies in the world. However, we have the highest level of expertise in the industry and need to look the most professional and high end. We have very relevant and important information to provide our customers about their compliance and projects. We will have the winning design coded to be an e-newsletter, so it needs to be one page. We want to keep our company colors and logo design in the newsletter, they are attached. We DO NOT want it to look like a mini-version of our website. We want a fresh look to this marketing piece. Newsletter will need to include title, possible sub-heading, space for a feature story, 2 other stories included, and space on either the left or right for short cuts, links or highlights of other articles. Contents/'In this issue' section, about us or branding area, section for relevant links, etc...
Pinnacle 300 companies, High-level management
Marketing

```html
<!DOCTYPE html>
<html lang="en">
<head>
<meta charset="utf-8">
<title>Foreign-Trade Zone News – Newsletter Layouts</title>
<link href="https://fonts.googleapis.com/css2?family=Roboto+Condensed:wght@300;400;700&family=Arimo:wght@400;700&display=swap" rel="stylesheet">
<style>
  :root{
    --backdrop:#9d9fa2;
    --paper:#ffffff;
    --ink:#222222;
    --forest:#1b4a22;
    --leaf:#6fbf4a;
    --khaki:#d4cd7f;
    --gold:#e8d640;
    --butter:#fcf3a8;
    --rule:#d9d2a4;
    --charcoal:#1d1d1d;
    --graphite:#2b2b2b;
    --mist:#e3e6e3;
  }
  *{box-sizing:border-box;margin:0;padding:0}
  html,body{width:1200px;height:900px;overflow:hidden;background:var(--backdrop)}
  body{position:relative;font-family:"Arimo",Arial,sans-serif;color:var(--ink)}
  .sheet{position:absolute;top:20px;width:522px;height:880px;background:var(--paper);overflow:hidden;box-shadow:0 0 6px rgba(0,0,0,.25)}
  .sheet--green{left:63px}
  .sheet--night{left:638px}
  .abs{position:absolute}

  /* masthead */
  .brand-panel{left:0;top:0;width:174px;height:118px;background:var(--charcoal);display:flex;align-items:center;justify-content:center;padding:0 18px}
  .brand-name{font-family:"Roboto Condensed",sans-serif;font-weight:400;font-size:17px;line-height:1.2;color:var(--mist);text-align:center}
  .banner{left:174px;top:0;width:348px;height:118px}
  .sheet--green .banner{background:linear-gradient(115deg,#0d3a14 0%,#1f6a2a 40%,#0f4118 60%,#236e2d 80%,#0b3210 100%)}
  .sheet--night .banner{background:linear-gradient(180deg,#2b5d6b 0%,#0f1e16 14%,#0b1a10 60%,#183b22 100%)}
  .sheet--night .brand-panel{background:linear-gradient(180deg,#263f47 0%,#111 10%,#1a1a1a 100%)}
  .issue-date{right:14px;top:18px;font-family:"Roboto Condensed",sans-serif;font-weight:700;font-size:10px;color:var(--gold)}
  .title-line{left:16px;top:36px;font-family:"Roboto Condensed",sans-serif;font-weight:400;font-size:33px;color:var(--mist);line-height:1}
  .title-news{left:16px;top:75px;font-family:"Roboto Condensed",sans-serif;font-weight:700;font-size:35px;color:var(--khaki);line-height:1}
  .tagline{left:106px;top:95px;font-family:"Roboto Condensed",sans-serif;font-weight:700;font-size:10px;color:var(--gold)}

  .social-bar{left:0;top:118px;width:174px;height:34px;background:var(--charcoal);display:flex;justify-content:center;align-items:center;gap:22px}
  .social-dot{width:12px;height:12px;border-radius:50%;background:var(--leaf)}
  .site-bar{left:0;top:152px;width:174px;height:31px;background:var(--graphite);text-align:center;line-height:31px;font-family:"Roboto Condensed",sans-serif;font-weight:700;font-size:11px;letter-spacing:.5px;color:var(--leaf)}
  .sheet--night .site-bar{background:#111;color:#fff}

  /* sidebar */
  .sidebar-rule{left:174px;top:118px;width:1px;height:762px;background:var(--rule)}
  .toc-item{left:0;width:174px;padding:0 23px}
  .toc-item--featured{background:var(--butter);padding-top:7px;height:49px}
  .toc-title{font-family:"Roboto Condensed",sans-serif;font-weight:700;font-size:13px;color:var(--forest);line-height:1.1}
  .toc-text{font-size:7.5px;line-height:10px;color:#222}
  .toc-end{left:0;top:385px;width:174px;height:1px;background:var(--rule)}

  .leader-photo{left:25px;top:406px;width:63px;height:63px;border-radius:50%;border:2px solid #333;background:radial-gradient(circle at 50% 40%,#d9b79c 0%,#a47e66 45%,#e8e6e0 75%)}
  .leader-name{left:98px;top:428px;font-family:"Roboto Condensed",sans-serif;font-weight:700;font-size:10.5px;color:var(--forest);line-height:1.1}
  .leader-role{font-weight:400;font-size:9.5px;color:#3b8a2e}
  .leader-note{left:23px;width:128px;font-size:8.3px;line-height:14.5px}

  .sidebar-divider{left:0;top:708px;width:174px;height:1px;background:var(--rule)}
  .about-title{left:23px;top:720px;font-family:"Roboto Condensed",sans-serif;font-weight:700;font-size:12.5px;color:var(--forest)}
  .about-icon{left:68px;top:742px}
  .about-head{left:23px;top:799px;font-weight:700;font-size:8.3px}
  .about-text{left:23px;top:813px;width:130px;font-size:8.3px;line-height:15px}

  /* main column */
  .headline{left:190px;font-family:"Roboto Condensed",sans-serif;font-weight:700;color:var(--forest);line-height:1.15}
  .headline--lead{top:135px;font-size:34px}
  .headline--second{top:404px;font-size:27px}
  .body-copy{left:190px;width:320px;font-size:10.6px;line-height:18px}
  .subhead{left:190px;top:471px;display:flex;align-items:center;gap:6px;font-family:"Arimo",Arial,sans-serif;font-weight:700;font-size:10.5px;color:var(--forest)}
  .read-more{left:188px;width:96px;height:22px;border:1px solid var(--khaki);font-size:10.5px;line-height:20px;padding-left:20px;color:var(--forest)}
  .read-more svg{position:absolute;left:-1px;top:-1px}
  .section-rule{left:174px;top:397px;width:348px;height:2px;background:#f0f0f0}

  .feature-photo{left:174px;top:710px;width:348px;height:124px;background:linear-gradient(120deg,#cfc6b8 0%,#a99a87 35%,#6d6d6a 60%,#d7d3ca 100%)}
  .feature-tag{left:188px;top:801px;height:21px;background:#262626;color:var(--butter);font-size:10.5px;line-height:21px;padding:0 14px 0 18px}
  .feature-band{left:174px;top:834px;width:348px;height:46px;background:var(--butter)}
  .feature-title{left:190px;top:838px;font-family:"Roboto Condensed",sans-serif;font-weight:700;font-size:34px;color:var(--forest);line-height:1.15}
  .feature-star{left:159px;top:692px}
</style>
</head>
<body>

<section class="sheet sheet--green">
  <div class="abs brand-panel"><div class="brand-name">Meridian Customs Group</div></div>
  <div class="abs banner">
    <div class="abs issue-date">16 APRIL 2014</div>
    <div class="abs title-line">Foreign-Trade Zone</div>
    <div class="abs title-news">NEWS</div>
    <div class="abs tagline">Important news about foreign-trade zones</div>
  </div>
  <div class="abs social-bar"><span class="social-dot"></span><span class="social-dot"></span><span class="social-dot"></span><span class="social-dot"></span></div>
  <div class="abs site-bar">www.meridiancustoms.com</div>
  <div class="abs sidebar-rule"></div>

  <div class="abs toc-item" style="top:195px"><div class="toc-title">ARTICLE 1</div><div class="toc-text">Editaquos rem restis dis imoditi ossitat aut aut pariberum fuga.</div></div>
  <div class="abs toc-item" style="top:243px"><div class="toc-title">ARTICLE 2</div><div class="toc-text">Editaquos rem restis dis imoditi ossitat aut aut pariberum fuga.</div></div>
  <div class="abs toc-item toc-item--featured" style="top:287px"><div class="toc-title">FEATURED STORY</div><div class="toc-text">Editaquos rem restis dis imoditi ossitat aut aut pariberum fuga.</div></div>
  <div class="abs toc-item" style="top:343px"><div class="toc-title">ARTICLE 3</div><div class="toc-text">Editaquos rem restis dis imoditi ossitat aut aut pariberum fuga.</div></div>
  <div class="abs toc-end"></div>

  <div class="abs leader-photo" role="img" aria-label="Portrait photo of the chief executive"></div>
  <div class="abs leader-name">DANA REYES<br><span class="leader-role">CEO</span></div>
  <p class="abs leader-note" style="top:478px">Editaquos rem restis dis imoditi ossitat urestius aut aut pariberum faccus doloribus aut prem repedis et eosam fuga. Giam quis quiae vel incid etur?</p>
  <p class="abs leader-note" style="top:565px">Erchiliquo culparciame nobitates ma por rem exerrun tibusti doluptiore dipsuntus Iciendant id quossedit, ius consequia debit alit expellore sin enet vendita sperfernamus autetur?</p>

  <div class="abs sidebar-divider"></div>
  <div class="abs about-title">ABOUT US</div>
  <svg class="abs about-icon" width="30" height="40" viewBox="0 0 30 40" fill="none" stroke="#b8a32a" stroke-width="1.6"><path d="M9 2c-2 3 2 4 0 7M14 2c-2 3 2 4 0 7M19 2c-2 3 2 4 0 7"/><path d="M2 14h22v10a9 9 0 0 1-9 9h-4a9 9 0 0 1-9-9z"/><path d="M24 17h2a3 3 0 0 1 0 6h-2"/><path d="M0 38h28"/></svg>
  <div class="abs about-head">OMNIHILLES DERORRO VLAUT</div>
  <p class="abs about-text">Accabor eperum esciasi maionemquo excea volupta tibusam, et aut es ut impellu ptiusam est, offictate volorec</p>

  <h1 class="abs headline headline--lead">HEADING TITLE OF<br>THE ARTICLE BELOW</h1>
  <p class="abs body-copy" style="top:220px">Lendae res nulpa cus, cum fugia volo quodipsus eiciis nullamus invera as et quiataq uoditin velent.<br>Editaquos rem restis dis imoditi ossitat urestius aut aut pariberum faccus doloribus aut prem repedis et eosam fuga. It ipsum et quas dolorporiate natur se dolore eum ent modigen dandand anditate eicat apiet eicit omnis eum, arum evernat emquisti sus.<br>Omnihilles derorro volo conse laut voloreh endite pre illa secabo.</p>
  <div class="abs read-more" style="top:352px"><svg width="14" height="22" viewBox="0 0 14 22" fill="none" stroke="#d4cd7f"><path d="M1 1l11 10L1 21"/></svg>READ MORE</div>
  <div class="abs section-rule"></div>

  <h2 class="abs headline headline--second">SMALLER HEADING TITLE<br>FOR LONGER TITLE TEXT</h2>
  <div class="abs subhead"><svg width="24" height="8" viewBox="0 0 24 8" fill="none" stroke="#5b7f4a" stroke-width="1.5"><path d="M0 4h22M18 1l4 3-4 3"/></svg>HERE IS POSSIBLE SUBHEADING</div>
  <p class="abs body-copy" style="top:492px">Lendae res nulpa cus, cum fugia volo quodipsus eiciis nullamus invera as et quiataq uoditin velent.<br>Editaquos rem restis dis imoditi ossitat urestius aut aut pariberum faccus doloribus aut prem repedis et eosam fuga. It ipsum et quas dolorporiate natur se dolore eum ent modigen dandand anditate eicat apiet eicit omnis eum, arum evernat emquisti sus.<br>Omnihilles derorro volo conse laut voloreh endite pre illa secabo.</p>
  <div class="abs read-more" style="top:652px"><svg width="14" height="22" viewBox="0 0 14 22" fill="none" stroke="#d4cd7f"><path d="M1 1l11 10L1 21"/></svg>READ MORE</div>

  <div class="abs feature-photo" role="img" aria-label="Photo of a team collaborating in a bright office"></div>
  <div class="abs feature-tag">FEATURED STORY</div>
  <div class="abs feature-band"></div>
  <h2 class="abs feature-title">HEADING TITLE OF</h2>
  <svg class="abs feature-star" width="32" height="32" viewBox="0 0 32 32"><path d="M16 1l4.4 9.6 10.4 1.1-7.8 7 2.2 10.3L16 23.8 6.8 29l2.2-10.3-7.8-7 10.4-1.1z" fill="#fbf29a" stroke="#d4c64a"/></svg>
</section>

<section class="sheet sheet--night">
  <div class="abs brand-panel"><div class="brand-name">Meridian Customs Group</div></div>
  <div class="abs banner">
    <div class="abs issue-date">16 APRIL 2014</div>
    <div class="abs title-line">Foreign-Trade Zone</div>
    <div class="abs title-news">NEWS</div>
    <div class="abs tagline">Important news about foreign-trade zones</div>
  </div>
  <div class="abs social-bar"><span class="social-dot"></span><span class="social-dot"></span><span class="social-dot"></span><span class="social-dot"></span></div>
  <div class="abs site-bar">www.meridiancustoms.com</div>
  <div class="abs sidebar-rule"></div>

  <div class="abs toc-item" style="top:195px"><div class="toc-title">ARTICLE 1</div><div class="toc-text">Editaquos rem restis dis imoditi ossitat aut aut pariberum fuga.</div></div>
  <div class="abs toc-item" style="top:243px"><div class="toc-title">ARTICLE 2</div><div class="toc-text">Editaquos rem restis dis imoditi ossitat aut aut pariberum fuga.</div></div>
  <div class="abs toc-item toc-item--featured" style="top:287px"><div class="toc-title">FEATURED STORY</div><div class="toc-text">Editaquos rem restis dis imoditi ossitat aut aut pariberum fuga.</div></div>
  <div class="abs toc-item" style="top:343px"><div class="toc-title">ARTICLE 3</div><div class="toc-text">Editaquos rem restis dis imoditi ossitat aut aut pariberum fuga.</div></div>
  <div class="abs toc-end"></div>

  <div class="abs leader-photo" role="img" aria-label="Portrait photo of the chief executive"></div>
  <div class="abs leader-name">DANA REYES<br><span class="leader-role">CEO</span></div>
  <p class="abs leader-note" style="top:478px">Editaquos rem restis dis imoditi ossitat urestius aut aut pariberum faccus doloribus aut prem repedis et eosam fuga. Giam quis quiae vel incid etur?</p>
  <p class="abs leader-note" style="top:565px">Erchiliquo culparciame nobitates ma por rem exerrun tibusti doluptiore dipsuntus Iciendant id quossedit, ius consequia debit alit expellore sin enet vendita sperfernamus autetur?</p>

  <div class="abs sidebar-divider"></div>
  <div class="abs about-title">ABOUT US</div>
  <svg class="abs about-icon" width="30" height="40" viewBox="0 0 30 40" fill="none" stroke="#b8a32a" stroke-width="1.6"><path d="M9 2c-2 3 2 4 0 7M14 2c-2 3 2 4 0 7M19 2c-2 3 2 4 0 7"/><path d="M2 14h22v10a9 9 0 0 1-9 9h-4a9 9 0 0 1-9-9z"/><path d="M24 17h2a3 3 0 0 1 0 6h-2"/><path d="M0 38h28"/></svg>
  <div class="abs about-head">OMNIHILLES DERORRO VLAUT</div>
  <p class="abs about-text">Accabor eperum esciasi maionemquo excea volupta tibusam, et aut es ut impellu ptiusam est, offictate volorec</p>

  <h1 class="abs headline headline--lead">HEADING TITLE OF<br>THE ARTICLE BELOW</h1>
  <p class="abs body-copy" style="top:220px">Lendae res nulpa cus, cum fugia volo quodipsus eiciis nullamus invera as et quiataq uoditin velent.<br>Editaquos rem restis dis imoditi ossitat urestius aut aut pariberum faccus doloribus aut prem repedis et eosam fuga. It ipsum et quas dolorporiate natur se dolore eum ent modigen dandand anditate eicat apiet eicit omnis eum, arum evernat emquisti sus.<br>Omnihilles derorro volo conse laut voloreh endite pre illa secabo.</p>
  <div class="abs read-more" style="top:352px"><svg width="14" height="22" viewBox="0 0 14 22" fill="none" stroke="#d4cd7f"><path d="M1 1l11 10L1 21"/></svg>READ MORE</div>
  <div class="abs section-rule"></div>

  <h2 class="abs headline headline--second">SMALLER HEADING TITLE<br>FOR LONGER TITLE TEXT</h2>
  <div class="abs subhead"><svg width="24" height="8" viewBox="0 0 24 8" fill="none" stroke="#5b7f4a" stroke-width="1.5"><path d="M0 4h22M18 1l4 3-4 3"/></svg>HERE IS POSSIBLE SUBHEADING</div>
  <p class="abs body-copy" style="top:492px">Lendae res nulpa cus, cum fugia volo quodipsus eiciis nullamus invera as et quiataq uoditin velent.<br>Editaquos rem restis dis imoditi ossitat urestius aut aut pariberum faccus doloribus aut prem repedis et eosam fuga. It ipsum et quas dolorporiate natur se dolore eum ent modigen dandand anditate eicat apiet eicit omnis eum, arum evernat emquisti sus.<br>Omnihilles derorro volo conse laut voloreh endite pre illa secabo.</p>
  <div class="abs read-more" style="top:652px"><svg width="14" height="22" viewBox="0 0 14 22" fill="none" stroke="#d4cd7f"><path d="M1 1l11 10L1 21"/></svg>READ MORE</div>

  <div class="abs feature-photo" role="img" aria-label="Photo of a team collaborating in a bright office"></div>
  <div class="abs feature-tag">FEATURED STORY</div>
  <div class="abs feature-band"></div>
  <h2 class="abs feature-title">HEADING TITLE OF</h2>
  <svg class="abs feature-star" width="32" height="32" viewBox="0 0 32 32"><path d="M16 1l4.4 9.6 10.4 1.1-7.8 7 2.2 10.3L16 23.8 6.8 29l2.2-10.3-7.8-7 10.4-1.1z" fill="#fbf29a" stroke="#d4c64a"/></svg>
</section>

</body>
</html>
```